Presentation pour application de menu digitale

Je souhaite créer un flyer de présentation pour une application de menu digitale afin de la présenter à mes futurs clients. Cette application aura aussi vocation de premier réseau social culinaire pour les utilisateurs finaux.
Merci de récupérer le texte du site platovia.app
Le flyer sera imprimé au format A3 pliable pour en faire un format A4.
Le logo et les images que vous récupérerez seront en vernis sélectif.

Target Market(s)

restaurateur

Industry/Entity Type

Restaurateur

Font styles to use
Sans Serif

Colors
59FF00
82FF00
B8FF75
E3FFCB
F4FFEA
6B429C
8869AF
B7A5CE
E3DAEB
F3F0F8

```html
<!DOCTYPE html>
<html lang="fr">
<head>
<meta charset="utf-8">
<title>Platovia – Flyer de présentation</title>
<link href="https://fonts.googleapis.com/css2?family=Josefin+Sans:wght@400;600;700&family=Quicksand:wght@400;500;700&display=swap" rel="stylesheet">
<style>
  :root{
    --bg:#dcdcde;
    --paper:#f6f6f6;
    --green:#52a985;
    --green-light:#62bb95;
    --purple:#6b429c;
    --purple-soft:#8869af;
    --ink:#2b2b33;
    --white:#ffffff;
  }
  *{margin:0;padding:0;box-sizing:border-box}
  html,body{width:857px;height:1200px;overflow:hidden;background:var(--bg)}
  .spread{
    position:absolute;left:18px;top:310px;width:820px;height:580px;
    background:var(--paper);box-shadow:0 10px 30px rgba(0,0,0,.15);overflow:hidden;
  }
  .page{position:absolute;top:0;width:410px;height:580px}
  .page--back{left:0;background:var(--green)}
  .page--cover{left:410px;background:var(--paper)}
  .wave{position:absolute;left:0;top:0;width:820px;height:580px;z-index:2}

  .benefits{position:absolute;left:34px;top:38px;width:350px;z-index:3;color:var(--white);font-family:"Quicksand",sans-serif}
  .benefits__title{font-family:"Josefin Sans",sans-serif;font-weight:700;color:var(--purple);font-size:19px;letter-spacing:.3px;text-transform:uppercase;line-height:1.1}
  .benefits__intro{font-size:8.5px;line-height:1.35;margin:4px 0 10px}
  .benefit{margin-bottom:7px}
  .benefit__name{font-family:"Josefin Sans",sans-serif;font-weight:700;color:var(--purple);font-size:10px}
  .benefit__text{font-size:8.5px;line-height:1.35}

  .cover{position:absolute;inset:0;z-index:3;font-family:"Josefin Sans",sans-serif;text-align:center}
  .cover__welcome{position:absolute;top:88px;left:0;right:0;font-size:10px;letter-spacing:3px;color:var(--ink);padding-left:70px}
  .brand{position:absolute;top:108px;left:0;right:0;padding-left:70px;display:flex;justify-content:center;align-items:center;gap:8px;font-weight:700;font-size:26px;color:var(--ink)}
  .brand__dot{width:14px;height:14px;border-radius:50%;background:var(--green-light)}
  .cover__kicker{position:absolute;top:160px;left:0;right:0;padding-left:70px;font-size:21px;color:var(--ink);letter-spacing:.5px}
  .cover__headline{position:absolute;top:184px;left:0;right:0;padding-left:70px;font-size:52px;font-weight:600;color:var(--purple);letter-spacing:1px;line-height:1}
  .cover__photo{position:absolute;left:70px;top:270px;width:320px;height:290px;z-index:1;border-radius:6px;
    background:radial-gradient(ellipse at 40% 35%,#f3d9a8 0%,#e9c7a4 28%,#f4ece8 55%,rgba(246,246,246,0) 78%)}
</style>
</head>
<body>
  <main class="spread">
    <section class="page page--back">
      <div class="benefits">
        <h2 class="benefits__title">Les avantages de l’application</h2>
        <p class="benefits__intro">Platovia combine les avantages d’un menu digital avec les interactions sociales pour transformer l’expérience culinaire en une aventure sociale et personnalisée.</p>
        <div class="benefit"><h3 class="benefit__name">1. Expérience client enrichie:</h3><p class="benefit__text">Permet aux clients de gérer leur expérience de restauration de manière ludique et interactive.</p></div>
        <div class="benefit"><h3 class="benefit__name">2. Réduction des temps d’attente:</h3><p class="benefit__text">Accélère le processus de commande grâce au pré-choix via l’application.</p></div>
        <div class="benefit"><h3 class="benefit__name">3. Amélioration de la fidélisation:</h3><p class="benefit__text">Les fonctionnalités de réseau social encouragent les clients à revenir et à inviter leurs amis.</p></div>
        <div class="benefit"><h3 class="benefit__name">4. Optimisation des opérations:</h3><p class="benefit__text">Aide le personnel à anticiper les besoins des clients pour une meilleure gestion des ressources.</p></div>
        <div class="benefit"><h3 class="benefit__name">5. Marketing ciblé et efficace:</h3><p class="benefit__text">Utilise les données collectées pour offrir des promotions personnalisées qui répondent aux préférences des clients.</p></div>
        <div class="benefit"><h3 class="benefit__name">6. Accroissement de la visibilité:</h3><p class="benefit__text">Le partage social par les utilisateurs agit comme un outil de marketing organique, augmentant la notoriété du restaurant.</p></div>
      </div>
    </section>

    <section class="page page--cover">
      <div class="cover__photo" role="img" aria-label="Photo d’une jeune femme souriante montrant l’application sur son smartphone"></div>
      <div class="cover">
        <p class="cover__welcome">BIENVENUE SUR</p>
        <div class="brand"><span class="brand__dot"></span><span class="brand__name">Platovia</span></div>
        <p class="cover__kicker">LE 1ER RÉSEAU SOCIAL</p>
        <h1 class="cover__headline">CULINAIRE</h1>
      </div>
    </section>

    <svg class="wave" viewBox="0 0 820 580" aria-hidden="true">
      <path d="M0,470 C40,430 90,405 150,412 C240,425 330,490 420,525 C480,548 530,568 570,580 L0,580 Z" fill="var(--green-light)"/>
      <path d="M0,470 C40,430 90,405 150,412 C240,425 330,490 420,525 C480,548 530,568 570,580" fill="none" stroke="var(--purple)" stroke-width="3"/>
    </svg>
  </main>
</body>
</html>
```